Varnex Consulting Business card design.

See our website www.varnexconsulting.example which will give you a good idea of what we are about. The font is called 'Play'.

I'd like a standout business card in keeping with the themes and branding on the website

Target Market(s)

professionals. HR directors

Industry/Entity Type

Business

Contact Information for Business Card

Varnex Consulting PO Box 3172 Merrowdale NSW 2291 1300 485 193 Gavin Threlkeld Principal email: career@varnexconsulting.example ABN: 71203948865

Font styles to use
Other font styles liked:
• Play

Requirements
Must have
• Must have same design colours and branding as website.
• On back I'd prefer a list of the things we do which appears below the name at the header on the website

```html
<!DOCTYPE html>
<html lang="en">
<head>
<meta charset="utf-8">
<title>Varnex Consulting – Business Card</title>
<link href="https://fonts.googleapis.com/css2?family=Montserrat:wght@300&family=Open+Sans:wght@400;700&display=swap" rel="stylesheet">
<style>
  :root {
    --backdrop: #2f2a27;
    --card-dark: #1c1d1f;
    --card-dark-edge: #262729;
    --brand-blue: #2e7fd1;
    --brand-blue-deep: #1f6ab8;
    --accent-blue: #2d86d6;
    --text-light: #e9ebee;
    --divider: #3a3c40;
  }
  * { box-sizing: border-box; margin: 0; padding: 0; }
  html, body { width: 1200px; height: 844px; overflow: hidden; }
  body {
    background: var(--backdrop);
    position: relative;
    font-family: "Open Sans", Arial, sans-serif;
  }
  .card {
    position: absolute;
    top: 263px;
    width: 520px;
    height: 318px;
    border-radius: 3px;
    overflow: hidden;
    box-shadow: 0 14px 30px rgba(0,0,0,.45);
  }
  .card--back {
    left: 50px;
    background: linear-gradient(135deg, var(--card-dark-edge), var(--card-dark));
  }
  .card--front {
    left: 630px;
    background: linear-gradient(135deg, var(--brand-blue), var(--brand-blue-deep));
  }
  .brand {
    position: absolute;
    display: flex;
    flex-direction: column;
    align-items: center;
    gap: 18px;
  }
  .brand__circle {
    border-radius: 50%;
    border: 3px solid currentColor;
  }
  .brand__name {
    font-family: "Montserrat", "Century Gothic", sans-serif;
    font-weight: 300;
    text-transform: uppercase;
    letter-spacing: 1px;
    white-space: nowrap;
  }
  .card--back .brand {
    left: 20px; top: 92px; width: 250px;
  }
  .card--back .brand__circle { width: 76px; height: 76px; color: var(--accent-blue); }
  .card--back .brand__name { color: var(--text-light); font-size: 20px; }
  .card--front .brand {
    left: 0; right: 0; top: 82px;
  }
  .card--front .brand__circle { width: 96px; height: 96px; color: #fff; }
  .card--front .brand__name { color: #fff; font-size: 27px; }
  .divider {
    position: absolute;
    left: 282px; top: 70px;
    width: 1px; height: 140px;
    background: var(--divider);
  }
  .contact {
    position: absolute;
    left: 296px; right: 14px; top: 66px;
    color: var(--text-light);
    font-size: 11.5px;
    line-height: 1.5;
    white-space: nowrap;
  }
  .contact__name {
    color: var(--accent-blue);
    font-weight: 700;
    font-size: 15px;
    line-height: 1.2;
  }
  .contact__role { margin-bottom: 14px; }
  .contact__abn { margin-bottom: 4px; }
  .contact__line { display: flex; align-items: center; gap: 7px; }
  .contact__line svg { width: 10px; height: 10px; flex: none; fill: var(--accent-blue); }
  .contact__address { margin-top: 6px; }
</style>
</head>
<body>
  <section class="card card--back" aria-label="Business card, contact side">
    <div class="brand">
      <div class="brand__circle"></div>
      <div class="brand__name">Varnex Consulting</div>
    </div>
    <div class="divider"></div>
    <div class="contact">
      <div class="contact__name">Gavin Threlkeld</div>
      <div class="contact__role">Principal</div>
      <div class="contact__abn">ABN: 71203948865</div>
      <div class="contact__line">
        <svg viewBox="0 0 10 10" aria-hidden="true"><path d="M2 0.5 L3.6 2.6 L2.7 3.7 C3.3 5 4.8 6.6 6.3 7.3 L7.4 6.4 L9.5 8 L8.4 9.5 C4.5 9.2 0.8 5.5 0.5 1.6 Z"/></svg>
        <span>1300 485 193</span>
      </div>
      <div class="contact__line">
        <svg viewBox="0 0 10 10" aria-hidden="true"><rect x="0.5" y="2" width="9" height="6.5"/></svg>
        <span>career@varnexconsulting.example</span>
      </div>
      <div class="contact__address">PO Box 3172 Merrowdale<br>NSW 2291</div>
    </div>
  </section>

  <section class="card card--front" aria-label="Business card, brand side">
    <div class="brand">
      <div class="brand__circle"></div>
      <div class="brand__name">Varnex Consulting</div>
    </div>
  </section>
</body>
</html>
```